Quillbrookes websites redesign

Www.quill-brookes.com needs to be redesigned along with updations. The incremental material will be provided for the updations. We are looking for complete redesign of the pages with the new content. The complete write up will be provided soon

Target Market(s)

Global

Coding

Coded - Design and coding required

Number of Pages Required

5+ page

Requirements
Must have
• A clean and slick design for the Consulting.
Should not have
• Too many pictures which reduces the speed of the site

```html
<!DOCTYPE html>
<html lang="en">
<head>
<meta charset="utf-8">
<title>Quillbrookes – Consultancy</title>
<link rel="stylesheet" href="https://fonts.googleapis.com/css2?family=Lato:ital,wght@0,400;0,700;1,400&family=Questrial&family=Open+Sans:wght@700&display=swap">
<style>
  :root {
    --navy: #253654;
    --maroon: #5e1f1f;
    --sky: #35a9e1;
    --ink: #222;
    --grey-band: #dadada;
    --text-grey: #777;
    --line: #e2e2e2;
    --white: #fff;
  }
  * { margin: 0; padding: 0; box-sizing: border-box; }
  html, body { width: 722px; height: 1200px; overflow: hidden; }
  body { position: relative; background: var(--white); font-family: "Lato", sans-serif; color: var(--ink); }
  .abs { position: absolute; }

  /* Header */
  .site-header { left: 0; top: 0; width: 722px; height: 73px; background: var(--navy); }
  .brand-box { left: 30px; top: 0; width: 195px; height: 73px; background: var(--white); display: flex; align-items: center; justify-content: center; gap: 7px; }
  .brand-dot { width: 26px; height: 26px; border-radius: 50%; background: var(--navy); }
  .brand-name { font-family: "Lato", sans-serif; font-size: 20px; color: var(--navy); }
  .nav-active-cap { left: 285px; top: 0; width: 36px; height: 3px; background: var(--white); }
  .nav-active-foot { left: 285px; top: 73px; width: 36px; height: 3px; background: var(--navy); z-index: 3; }
  .nav-item { top: 33px; font-size: 8px; color: var(--white); text-transform: uppercase; letter-spacing: .1px; }
  .nav-item.is-active { color: var(--sky); }

  /* Hero */
  .hero { left: 0; top: 73px; width: 722px; height: 349px; background: linear-gradient(90deg, #e6eef6 0%, #f4f7fb 40%, #eef3f8 100%); }
  .hero-photo { left: 320px; top: 73px; width: 402px; height: 349px; background: linear-gradient(160deg, #e9eef4 0%, #c9d3df 45%, #2f3e5e 80%, #1f2b45 100%); }
  .hero-title { left: 32px; top: 194px; font-family: "Questrial", sans-serif; font-size: 23px; color: var(--navy); font-weight: 400; letter-spacing: .2px; }
  .hero-text { left: 32px; top: 229px; width: 284px; font-size: 8.4px; line-height: 13.6px; color: #333; text-align: justify; }
  .btn { background: var(--navy); color: var(--white); font-size: 8px; text-transform: uppercase; display: flex; align-items: center; justify-content: center; }
  .hero-btn { left: 32px; top: 295px; width: 74px; height: 23px; }

  /* Range band */
  .range-band { left: 0; top: 422px; width: 722px; height: 87px; background: var(--grey-band); }
  .range { width: 110px; height: 110px; border-radius: 50%; border: 1px solid; display: flex; align-items: center; justify-content: center; background: transparent; }
  .range-core { width: 94px; height: 94px; border-radius: 50%; display: flex; align-items: center; justify-content: center; font-family: "Open Sans", sans-serif; font-weight: 700; font-size: 16px; color: var(--white); }

  /* About */
  .about-title { left: 0; top: 530px; width: 722px; text-align: center; font-family: "Questrial", sans-serif; font-size: 21px; color: var(--navy); }
  .rule { height: 1px; background: var(--line); }
  .about-copy { left: 78px; width: 566px; text-align: center; font-size: 7.8px; line-height: 14.7px; color: var(--text-grey); }
  .about-btn { left: 321px; top: 718px; width: 81px; height: 24px; }

  /* Testimonials */
  .testimonials { left: 0; top: 767px; width: 722px; height: 216px; background: var(--navy); }
  .testi-title { left: 0; top: 785px; width: 722px; text-align: center; font-family: "Questrial", sans-serif; font-size: 20px; color: var(--white); }
  .quote-card { left: 221px; top: 841px; width: 241px; height: 103px; background: var(--white); padding: 25px 14px 0 14px; font-size: 7px; line-height: 13.6px; color: #999; font-style: italic; }
  .quote-mark { font-family: Georgia, serif; font-size: 46px; color: #c8c8c8; line-height: 1; }
  .avatar { left: 506px; top: 848px; width: 48px; height: 48px; border-radius: 50%; border: 2px solid #111; background: radial-gradient(circle at 50% 40%, #c7a68c 0%, #8c6b57 55%, #2c3a55 100%); }
  .testi-name { left: 470px; top: 898px; width: 120px; text-align: center; font-family: "Lato", sans-serif; font-size: 14px; color: var(--sky); }
  .testi-place { left: 470px; top: 917px; width: 120px; text-align: center; font-size: 7.5px; color: #b8c0cc; }

  /* Footer */
  .footer-brand { left: 40px; top: 1045px; display: flex; align-items: center; gap: 8px; }
  .footer-brand .brand-name { font-size: 21px; }
  .footer-brand .brand-dot { width: 28px; height: 28px; }
  .col-sep { top: 999px; width: 1px; height: 125px; background: var(--line); }
  .col-title { top: 1007px; font-family: "Questrial", sans-serif; font-size: 10.5px; color: var(--maroon); }
  .link-list { list-style: none; font-size: 7.3px; color: #999; }
  .link-list li { height: 17.2px; }
  .link-list li::before { content: "•"; color: #bbb; margin-right: 5px; }

  .bottom-bar { left: 0; top: 1142px; width: 722px; height: 58px; background: var(--navy); }
  .copyright { left: 0; top: 1168px; width: 754px; text-align: center; font-size: 7px; color: var(--white); }
  .social { top: 1162px; width: 18px; height: 17px; border: 1px solid #8fa3c4; }
  .social.is-filled { background: var(--sky); border-color: var(--sky); }
</style>
</head>
<body>

  <!-- Header -->
  <header class="abs site-header"></header>
  <div class="abs brand-box"><span class="brand-dot"></span><span class="brand-name">Quillbrookes</span></div>
  <div class="abs nav-active-cap"></div>
  <nav>
    <span class="abs nav-item is-active" style="left:292px">Home</span>
    <span class="abs nav-item" style="left:346px">Founder</span>
    <span class="abs nav-item" style="left:414px">Consultancy</span>
    <span class="abs nav-item" style="left:502px">System</span>
    <span class="abs nav-item" style="left:562px">Case Studies</span>
    <span class="abs nav-item" style="left:646px">Contact Us</span>
  </nav>

  <!-- Hero -->
  <section class="abs hero"></section>
  <div class="abs hero-photo" role="img" aria-label="Photo of three business people in suits working at a laptop in a bright office"></div>
  <div class="abs nav-active-foot"></div>
  <h1 class="abs hero-title">Welcome to Quillbrookes</h1>
  <p class="abs hero-text">Lorem ipsum dolor sit amet, consectetur adipiscing elit, sed do eiusmod tempor incididunt ut labore et dolore magna aliqua. Ut enim ad minim veniam, quis nostrud exercitation ullamco laboris nisi ut aliquip ex ea commodo consequat. Deserunt mollit anim id est laborum.</p>
  <a class="abs btn hero-btn">Read More</a>

  <!-- Size ranges -->
  <div class="abs range-band"></div>
  <div class="abs range" style="left:83px;top:368px;border-color:#111"><div class="range-core" style="background:#000">0-250</div></div>
  <div class="abs range" style="left:235px;top:368px;border-color:var(--maroon)"><div class="range-core" style="background:var(--maroon)">250 - 500</div></div>
  <div class="abs range" style="left:378px;top:368px;border-color:var(--sky)"><div class="range-core" style="background:var(--sky)">500 - 1000</div></div>
  <div class="abs range" style="left:524px;top:368px;border-color:var(--navy)"><div class="range-core" style="background:var(--navy)">&gt;1000</div></div>

  <!-- About -->
  <div class="abs rule" style="left:29px;top:546px;width:273px"></div>
  <div class="abs rule" style="left:418px;top:546px;width:274px"></div>
  <h2 class="abs about-title">About Us</h2>
  <p class="abs about-copy" style="top:570px">Quillbrookes Consultancy Limited capitalizes on synergies arising from trade and investment linkages between countries and knowledge of traditional and non-traditional pools of liquidity to provide consultancy services to Emerging country banks, Corporates and SMEs.</p>
  <p class="abs about-copy" style="top:615px">The Consultancy provides bank neutral views to Corporates and SMEs in Asian emerging markets and helps in improving financial structure and efficient use of funds. Our endeavor is to provide a distinct bottom line advantage to our clients. The primary focus is in regionalisation of the banking relationship across the globe, providing structured finance solutions and off balance sheet solutions.</p>
  <p class="abs about-copy" style="top:674px">The consultancy for the Banks and Non Banking Financial Institutions is focused on risk mitigation techniques, Export Credit Agency business and trade origination and distribution strategies along with raising long term liabilities.</p>
  <a class="abs btn about-btn">Read More</a>

  <!-- Testimonials -->
  <section class="abs testimonials"></section>
  <h2 class="abs testi-title">Our Testimonials</h2>
  <svg class="abs" style="left:120px;top:861px" width="24" height="64" viewBox="0 0 24 64"><polyline points="22,1 2,32 22,63" fill="none" stroke="#dfe5ee" stroke-width="1.3"/></svg>
  <svg class="abs" style="left:621px;top:858px" width="24" height="64" viewBox="0 0 24 64"><polyline points="2,1 22,32 2,63" fill="none" stroke="#dfe5ee" stroke-width="1.3"/></svg>
  <span class="abs quote-mark" style="left:216px;top:828px">&ldquo;</span>
  <div class="abs quote-card">Lorem ipsum dolor sit amet, consectetur adipiscing elit, sed do eiusmod tempor incididunt ut labore et dolore magna aliqua. Ut enim ad minim veniam, quis nostrud exercitation ullamco laboris nisi ut aliquip ex ea commodo consequat.</div>
  <svg class="abs" style="left:461px;top:862px" width="16" height="22" viewBox="0 0 16 22"><polygon points="0,0 15,2 0,20" fill="#fff"/></svg>
  <span class="abs quote-mark" style="left:436px;top:922px">&rdquo;</span>
  <div class="abs avatar" role="img" aria-label="Client portrait"></div>
  <div class="abs testi-name">Alex Rowan</div>
  <div class="abs testi-place">City Location</div>

  <!-- Footer -->
  <div class="abs footer-brand"><span class="brand-dot"></span><span class="brand-name">Quillbrookes</span></div>
  <div class="abs col-sep" style="left:230px"></div>
  <div class="abs col-sep" style="left:399px"></div>
  <div class="abs col-sep" style="left:569px"></div>

  <h3 class="abs col-title" style="left:250px">Important Links</h3>
  <ul class="abs link-list" style="left:249px;top:1030px">
    <li>Affiliate Program</li><li>Special Promotions</li><li>Newsletter</li><li>Contact</li>
  </ul>
  <h3 class="abs col-title" style="left:418px">Categories</h3>
  <ul class="abs link-list" style="left:419px;top:1030px">
    <li>Webmail Login</li><li>Account Login</li><li>FAQs</li><li>Server References</li>
  </ul>
  <h3 class="abs col-title" style="left:590px">Navigation</h3>
  <ul class="abs link-list" style="left:589px;top:1030px">
    <li>About Us</li><li>Founder</li><li>Cosultancy</li><li>System</li><li>Contact Us</li>
  </ul>

  <footer class="abs bottom-bar"></footer>
  <p class="abs copyright">Copyright 2015 Company Name.&nbsp; All Rights Reserved.</p>
  <span class="abs social" style="left:630px" aria-label="Social link"></span>
  <span class="abs social is-filled" style="left:656px" aria-label="Social link"></span>
  <span class="abs social" style="left:682px" aria-label="Social link"></span>

</body>
</html>
```